KVOR Individual and Corporate Development Business Card Design

KVOR needs a business card design that is aligned with it's values and targetted markets. Coherent Lattice of Adaptive Reasoning Method's self diagnosis model and tools, which can be used for personal improvement and team/business performance enhancement, is based on the learnings of over 20 years of medical practitioning. KVOR supercharges personal effectiveness and awareness to also increase team and business performance.

The targetted markets are high performance individuals and teams who aspire seek to enhance their capabilities and achieve their absolute best potential.

Look and feel for the business card design we are looking for is high technology, premium, fresh, new and medical.

Target Market(s)

Industry/Entity Type

Business Consultant

Contact Information for Business Card

Logo, Full Name, Title, Phone number, Email, company name, Address,

Font styles to use
Sans Serif

Requirements
Must have
• Tag line: Elevating Clarity and Drive for Ambitious Achievers
• Please use same colours as the logo.

```html
<!DOCTYPE html>
<html lang="en">
<head>
<meta charset="utf-8">
<title>KVOR Business Card</title>
<link href="https://fonts.googleapis.com/css2?family=Source+Sans+3:wght@400;600;700&display=swap" rel="stylesheet">
<style>
  :root {
    --teal: #05a9c2;
    --ink: #1d1d1d;
    --paper: #ffffff;
    --stage: #000000;
  }
  html, body {
    margin: 0;
    width: 1200px;
    height: 900px;
    overflow: hidden;
    background: var(--stage);
    font-family: "Source Sans 3", sans-serif;
  }
  .canvas { position: relative; width: 1200px; height: 900px; }

  .card {
    position: absolute;
    width: 477px;
    height: 293px;
    overflow: hidden;
  }
  .card-front {
    left: 116px; top: 275px;
    background: var(--paper);
    border-radius: 0 58px 0 58px;
  }
  .card-back {
    left: 622px; top: 276px;
    height: 292px;
    background: var(--teal);
    border-radius: 58px 0 58px 0;
  }

  .wordmark {
    position: absolute;
    font-weight: 700;
    color: var(--teal);
    line-height: 1;
  }
  .wordmark .name { display: block; letter-spacing: 2px; }
  .wordmark .full {
    display: block;
    text-transform: uppercase;
    letter-spacing: 0.3px;
  }
  .card-front .wordmark { left: 54px; top: 76px; }
  .card-front .wordmark .name { font-size: 52px; margin-bottom: 8px; }
  .card-front .wordmark .full { font-size: 12.5px; line-height: 13px; }

  .card-back .wordmark { left: 0; width: 477px; top: 98px; text-align: center; color: var(--paper); }
  .card-back .wordmark .name { font-size: 64px; margin-bottom: 4px; }
  .card-back .wordmark .full { font-size: 14.5px; line-height: 15px; }

  .person { position: absolute; right: 19px; top: 33px; text-align: right; }
  .person .full-name { font-size: 21px; font-weight: 700; color: var(--teal); line-height: 24px; }
  .person .role { font-size: 13.5px; color: var(--ink); line-height: 17px; }

  .address {
    position: absolute; right: 21px; top: 157px;
    text-align: right; font-size: 13.5px; line-height: 17px; color: var(--ink);
  }
  .contacts {
    position: absolute; right: 19px; top: 217px;
    list-style: none; margin: 0; padding: 0;
    font-size: 13.5px; line-height: 17.5px; color: var(--ink);
  }
  .contacts li { display: flex; justify-content: flex-end; align-items: center; gap: 7px; }
  .contacts svg { width: 11px; height: 11px; fill: var(--teal); }

  .tagline-band {
    position: absolute; left: 0; top: 210px;
    width: 477px; height: 56px;
    background: var(--paper);
    display: flex; align-items: center; justify-content: center;
    text-align: center;
    color: var(--teal); font-weight: 600; font-size: 14.5px; line-height: 17px;
    text-transform: uppercase; letter-spacing: 0.2px;
  }
</style>
</head>
<body>
<main class="canvas">

  <section class="card card-front" aria-label="Business card front">
    <div class="wordmark">
      <span class="name">KVOR</span>
      <span class="full">Coherent Lattice of Adaptive<br>Reasoning Method</span>
    </div>

    <div class="person">
      <div class="full-name">Daniel Marsh</div>
      <div class="role">Managing Director</div>
    </div>

    <div class="address">48, Harbour Lane<br>Country Name, 123456</div>

    <ul class="contacts">
      <li>044-987 654 321
        <svg viewBox="0 0 24 24" aria-hidden="true"><path d="M6.6 10.8a15.1 15.1 0 0 0 6.6 6.6l2.2-2.2c.3-.3.7-.4 1-.2 1.1.4 2.3.6 3.6.6.6 0 1 .4 1 1V20c0 .6-.4 1-1 1A17 17 0 0 1 3 4c0-.6.4-1 1-1h3.5c.6 0 1 .4 1 1 0 1.3.2 2.5.6 3.6.1.3 0 .7-.2 1z"/></svg>
      </li>
      <li>hello@kvormail.com
        <svg viewBox="0 0 24 24" aria-hidden="true"><path d="M2 5h20v14H2z" fill="var(--teal)"/><path d="M3 6.5l9 6.5 9-6.5" fill="none" stroke="#fff" stroke-width="1.6"/></svg>
      </li>
      <li>www.kvorsite.com
        <svg viewBox="0 0 24 24" aria-hidden="true" style="fill:none;stroke:var(--teal);stroke-width:2.6;stroke-linecap:round"><path d="M10 14a4.5 4.5 0 0 0 6.4 0l3.3-3.3a4.5 4.5 0 0 0-6.4-6.4L12 5.6"/><path d="M14 10a4.5 4.5 0 0 0-6.4 0l-3.3 3.3a4.5 4.5 0 0 0 6.4 6.4l1.3-1.3"/></svg>
      </li>
    </ul>
  </section>

  <section class="card card-back" aria-label="Business card back">
    <div class="wordmark">
      <span class="name">KVOR</span>
      <span class="full">Coherent Lattice of Adaptive<br>Reasoning Method</span>
    </div>
    <div class="tagline-band">Elevating Clarity and Drive<br>for Ambitious Achievers</div>
  </section>

</main>
</body>
</html>
```